SaaS Early tech startup business card design

Unique design for experience ecommerce platform company. the business cards will be used by executive members. conformance with color code is required.

```html
<!DOCTYPE html>
<html lang="en">
<head>
<meta charset="utf-8">
<title>Kelvo — Business Card</title>
<link rel="stylesheet" href="https://fonts.googleapis.com/css2?family=Source+Sans+3:wght@400;600;700&family=Montserrat:wght@600;800&display=swap">
<style>
  :root {
    --stage: #2b2c2e;
    --card: #1c1d1f;
    --card-back: #18191b;
    --teal: #17a6a3;
    --teal-bright: #20b9ad;
    --text-grey: #c9cbcd;
    --rule: #8a8c8f;
    --pattern: #222326;
  }
  * { box-sizing: border-box; margin: 0; padding: 0; }
  html, body {
    width: 1200px;
    height: 1108px;
    overflow: hidden;
    background: var(--stage);
  }
  .stage {
    position: relative;
    width: 1200px;
    height: 1108px;
    display: flex;
    justify-content: center;
    align-items: center;
    gap: 70px;
  }
  .card {
    width: 430px;
    height: 752px;
    border-radius: 24px;
    position: relative;
    overflow: hidden;
    box-shadow: 0 18px 40px rgba(0,0,0,0.45);
  }
  .card--front {
    background: var(--card);
    display: flex;
    flex-direction: column;
    align-items: center;
    font-family: "Source Sans 3", sans-serif;
  }
  .brand-name {
    font-family: "Montserrat", sans-serif;
    font-weight: 800;
    color: var(--teal);
    letter-spacing: -2px;
    line-height: 1;
  }
  .card--front .brand-name {
    font-size: 128px;
    margin-top: 150px;
  }
  .person {
    margin-top: 178px;
    text-align: center;
  }
  .person__name {
    font-family: "Montserrat", sans-serif;
    font-weight: 600;
    font-size: 25px;
    color: var(--teal);
    letter-spacing: 0.5px;
    text-transform: uppercase;
  }
  .person__role {
    font-size: 20px;
    color: var(--text-grey);
    margin-top: 2px;
  }
  .icon-row {
    display: flex;
    align-items: center;
    gap: 6px;
    margin-top: 20px;
    width: 300px;
  }
  .icon-row__rule {
    flex: 1;
    height: 1px;
    background: var(--rule);
  }
  .icon-box {
    width: 32px;
    height: 32px;
    border-radius: 5px;
    background: var(--teal);
    display: flex;
    align-items: center;
    justify-content: center;
  }
  .icon-box svg { width: 20px; height: 20px; }
  .contact {
    list-style: none;
    margin-top: 14px;
    text-align: center;
    font-size: 21px;
    line-height: 1.32;
    color: var(--text-grey);
  }
  .divider {
    width: 300px;
    height: 1px;
    background: var(--rule);
    margin-top: 16px;
  }
  .address {
    font-style: normal;
    margin-top: 14px;
    text-align: center;
    font-size: 21px;
    line-height: 1.32;
    color: var(--text-grey);
  }
  .card--back {
    background: var(--card-back);
  }
  .back-texture {
    position: absolute;
    inset: 0;
    background: linear-gradient(160deg, var(--pattern) 0%, var(--card-back) 75%);
  }
  .card--back .brand-name {
    position: absolute;
    right: 48px;
    bottom: 150px;
    font-size: 52px;
    letter-spacing: -1px;
  }
</style>
</head>
<body>
<main class="stage">
  <section class="card card--front" aria-label="Card front">
    <div class="brand-name">Kelvo</div>

    <div class="person">
      <h1 class="person__name">Marcus Hale</h1>
      <p class="person__role">Managing Director</p>
    </div>

    <div class="icon-row">
      <span class="icon-row__rule"></span>
      <span class="icon-box" aria-label="Phone">
        <svg viewBox="0 0 24 24" fill="none" stroke="#0d3f45" stroke-width="2" stroke-linecap="round" stroke-linejoin="round">
          <path d="M5 4h4l2 5-2.5 1.5a11 11 0 0 0 5 5L15 13l5 2v4a2 2 0 0 1-2 2A16 16 0 0 1 3 6a2 2 0 0 1 2-2z"/>
        </svg>
      </span>
      <span class="icon-box" aria-label="Email">
        <svg viewBox="0 0 24 24" fill="none" stroke="#0d3f45" stroke-width="2" stroke-linejoin="round">
          <rect x="3" y="6" width="18" height="12" rx="1"/>
          <path d="M3 6l9 7 9-7"/>
        </svg>
      </span>
      <span class="icon-box" aria-label="Website">
        <svg viewBox="0 0 24 24" fill="none" stroke="#0d3f45" stroke-width="2">
          <circle cx="12" cy="12" r="8.5"/>
          <path d="M3.5 12h17M12 3.5c3 3 3 14 0 17M12 3.5c-3 3-3 14 0 17"/>
        </svg>
      </span>
      <span class="icon-row__rule"></span>
    </div>

    <ul class="contact">
      <li>031-555 204 816</li>
      <li>hello@kelvo.io</li>
      <li>www.kelvo.io</li>
    </ul>

    <div class="divider"></div>

    <address class="address">
      88, Harbor Lane West<br>
      30917, Northland
    </address>
  </section>

  <section class="card card--back" aria-label="Card back">
    <div class="back-texture" role="img" aria-label="Faint tone-on-tone repeated brand name pattern"></div>
    <div class="brand-name">Kelvo</div>
  </section>
</main>
</body>
</html>
```